New Fresh design for online Rabbit Game

Hi,

we are a french company working on a online rabbits game for kids, and not kids.

Our website is www.zorvelo.fr, but you can look at the US version : www.quintamble.com

We buy our actual design 2 years ago, but we now think it's too boring and washed out...

We need yours talent to make a really more exacting, more colorful, fresh and dynamic design.

In our game, players have to breed and train rabbits and to make them run races. Players run again friends or players.

Players are kids, between 8 and 15 years. But best players are often parents of these kids !

Our ambiance is clearly funny. We really like if color theme or background look like a nice blue sky, and / or beach. Something that make people happy to come, and say "You are here on holly days to have fun !"

I think the best is if we have 2 layouts, one for the Home page, and one for all other page.

For home page, we are really open to any proposition, we just need to keep our features :
- registration (with rabbit preview)
- connection
- game preview (images slide with small text)
- live race preview (as we have actually)

For other pages layout, we need a layout with a standard container (maybe 850 px width?), and our 2 navigation's bar.

We only need psd, no html integration.

Thanks for your help, please ask me for any questions.
Updates

Hi, 

I have just added some information, concerning layout.

Also we have just committed the budget.

Target Market(s)

Mostly kids between 8 and 15 years.

Industry/Entity Type

It Company

Requirements
Must have
• We already have some characters, like Mr Wimble at the home page and our rabbits. We want to keep all of them, so new design have to match with there style (carton).

If you create an account, you will see we have a big nav bar with 6 tabs, and a little top bar. We absolutely need them to keep a easy navigation in website.

We also need some proposition of element style, like h1, h2, h3, hr, inputs, buttons, notification bubble, etc... So we can work to improve all our pages.
Nice to have
• I think the actual website is a little to wide (about 1000px width). Maybe something like 900px - 850px is more elegant ?
In this case, we can arrange pages to deal with it.

It can be cool if major colors are stil blue and green, to match a little with actual colors. But it's no very important.
Should not have
• We don't want too big header picture (for the all pages layout). I mean, players have to focus on the content.

We don't want photo realistic style, our style is cartoon.

We don't want flash. But Js animations are ok.

```html
<!DOCTYPE html>
<html lang="en">
<head>
<meta charset="utf-8">
<title>Quintamble – Home</title>
<link rel="stylesheet" href="https://fonts.googleapis.com/css2?family=Ubuntu:wght@400;500;700&family=Open+Sans:wght@400;600&display=swap">
<style>
  :root {
    --sky-top: #5fd0ea;
    --sky-low: #b9ecf7;
    --sea: #2fb4d8;
    --sand: #f6dfae;
    --green-dark: #7fb21c;
    --green-mid: #9dcb2c;
    --green-light: #c4e36a;
    --panel: #eef3dc;
    --panel-edge: #dfe9b8;
    --nav-top: #e6f4b8;
    --nav-bottom: #c7e27a;
    --nav-text: #4d6b12;
    --orange: #f07a0a;
    --orange-dark: #d25f00;
    --blue: #1a8cc4;
    --text: #3c4420;
    --white: #ffffff;
    --video: #000000;
  }
  * { box-sizing: border-box; margin: 0; padding: 0; }
  html, body { width: 1200px; height: 1025px; overflow: hidden; }
  body { font-family: "Ubuntu", sans-serif; color: var(--text); }

  .canvas { position: relative; width: 1200px; height: 1025px; overflow: hidden; }

  .scenery {
    position: absolute; inset: 0;
    background: linear-gradient(180deg, var(--sky-top) 0%, var(--sky-low) 58%, var(--sea) 60%, var(--sea) 63%, var(--sand) 65%, var(--sand) 100%);
  }

  .brand {
    position: absolute; left: 164px; top: 38px; display: flex; align-items: center; gap: 14px;
  }
  .brand-mark { width: 34px; height: 34px; border-radius: 50%; background: var(--white); }
  .brand-name { font-weight: 700; font-size: 38px; color: var(--orange); }

  .board {
    position: absolute; left: 161px; top: 139px; width: 874px; height: 773px;
    background: linear-gradient(160deg, var(--green-mid) 0%, var(--green-light) 40%, var(--green-dark) 100%);
    border-radius: 6px; box-shadow: 0 3px 10px rgba(0,0,0,.3);
  }

  .main-nav { position: absolute; left: 24px; top: 15px; display: flex; gap: 10px; list-style: none; }
  .main-nav li {
    width: 138px; height: 36px; line-height: 36px; text-align: center;
    background: linear-gradient(180deg, var(--nav-top), var(--nav-bottom));
    border-radius: 3px; color: var(--nav-text); font-size: 15px; font-weight: 500;
    box-shadow: 0 1px 2px rgba(0,0,0,.15);
  }

  .tagline { position: absolute; left: 24px; top: 87px; color: var(--white); font-size: 18px; font-weight: 500; }

  .panel {
    position: absolute; background: linear-gradient(180deg, var(--panel), var(--panel-edge));
    border: 2px solid var(--green-light); border-radius: 6px;
  }
  .panel h2 { font-size: 18px; font-weight: 500; color: var(--orange); }

  .register { left: 24px; top: 123px; width: 418px; height: 216px; }
  .login { left: 449px; top: 123px; width: 416px; height: 216px; }
  .overview { left: 26px; top: 356px; width: 417px; height: 367px; }
  .races { left: 450px; top: 356px; width: 416px; height: 367px; }

  .register h2 { position: absolute; left: 15px; top: 32px; }
  .step { position: absolute; font-size: 12px; color: var(--blue); }
  .hint { position: absolute; left: 226px; top: 30px; font-size: 12px; font-weight: 500; color: var(--orange); line-height: 19px; }
  .pet-name { position: absolute; left: 15px; top: 93px; font-family: "Open Sans", sans-serif; font-size: 10px; }
  .pet-preview {
    position: absolute; left: 10px; top: 115px; width: 60px; height: 55px; border-radius: 20px;
    background: radial-gradient(circle, #e6e3d6, #cfcab8);
  }
  .picker { position: absolute; left: 90px; top: 118px; list-style: none; }
  .picker li { display: flex; align-items: center; justify-content: space-between; width: 90px; height: 21px; font-size: 11px; }
  .text-field { position: absolute; height: 23px; background: var(--white); border: 1px solid #c9cfb4; border-radius: 2px; }
  .btn {
    position: absolute; height: 24px; padding: 0 16px; line-height: 24px;
    background: linear-gradient(180deg, #ff9324, var(--orange-dark));
    color: var(--white); font-size: 13px; font-weight: 500; border-radius: 2px;
  }

  .mascot {
    position: absolute; left: 22px; top: 28px; width: 130px; height: 178px; border-radius: 50% 50% 40% 40%;
    background: linear-gradient(180deg, #6f8e2e, #9fbf3a 60%, #f0d23b);
  }
  .login h2 { position: absolute; left: 172px; top: 34px; color: var(--blue); }
  .field-label { position: absolute; font-size: 12px; }

  .overview h2 { position: absolute; left: 16px; top: 22px; }
  .tabs { position: absolute; left: 16px; top: 58px; display: flex; gap: 15px; list-style: none; font-size: 12px; font-weight: 500; }
  .tabs .active { color: var(--blue); }
  .preview-shot {
    position: absolute; left: 16px; top: 82px; width: 378px; height: 196px; border-radius: 3px;
    background: linear-gradient(135deg, #7dbb30, #c9d964 45%, #e3c97a 60%, #8dbb3a);
  }
  .overview p { position: absolute; left: 19px; top: 293px; width: 380px; font-family: "Open Sans", sans-serif; font-size: 10.5px; line-height: 19px; }

  .races h2 { position: absolute; left: 16px; top: 22px; }
  .live-video { position: absolute; left: 13px; top: 56px; width: 388px; height: 266px; background: var(--video); border-radius: 2px; }
  .live-video svg { position: absolute; left: 174px; top: 107px; }

  .site-footer {
    position: absolute; left: 24px; top: 736px; width: 842px; height: 36px; line-height: 36px; padding-left: 25px;
    background: linear-gradient(180deg, var(--nav-top), var(--nav-bottom)); border-radius: 3px;
    font-size: 10.5px; font-weight: 500; color: var(--nav-text);
  }
</style>
</head>
<body>
<div class="canvas">
  <div class="scenery" role="img" aria-label="Cartoon beach backdrop with sunny blue sky, clouds, sea, palm tree and surfboards"></div>

  <div class="brand">
    <span class="brand-mark"></span>
    <span class="brand-name">Quintamble</span>
  </div>

  <main class="board">
    <ul class="main-nav">
      <li>Accueil</li><li>News</li><li>Forum</li><li>Recprd</li><li>Aide</li>
    </ul>

    <p class="tagline">The coolest racing and breeding game there is</p>

    <section class="panel register">
      <h2>New player</h2>
      <p class="step" style="left:15px;top:72px">1 - Choose your bunny</p>
      <p class="pet-name">Guimauve</p>
      <div class="pet-preview" role="img" aria-label="Cartoon bunny preview"></div>
      <ul class="picker">
        <li><svg width="16" height="12"><path d="M0 6 L7 0 V4 H16 V8 H7 V12Z" fill="#8cc43a"/></svg>Original<svg width="16" height="12"><path d="M16 6 L9 0 V4 H0 V8 H9 V12Z" fill="#8cc43a"/></svg></li>
        <li><svg width="16" height="12"><path d="M0 6 L7 0 V4 H16 V8 H7 V12Z" fill="#8cc43a"/></svg>Gray<svg width="16" height="12"><path d="M16 6 L9 0 V4 H0 V8 H9 V12Z" fill="#8cc43a"/></svg></li>
        <li><svg width="16" height="12"><path d="M0 6 L7 0 V4 H16 V8 H7 V12Z" fill="#8cc43a"/></svg>Male<svg width="16" height="12"><path d="M16 6 L9 0 V4 H0 V8 H9 V12Z" fill="#8cc43a"/></svg></li>
      </ul>
      <p class="hint">Register in just a couple<br>of seconds!</p>
      <p class="step" style="left:225px;top:76px">2- Choose a username</p>
      <div class="text-field" style="left:228px;top:98px;width:167px"></div>
      <p class="step" style="left:225px;top:136px;font-weight:500">3- OK! We're good to go!</p>
      <span class="btn" style="left:228px;top:158px">Play</span>
    </section>

    <section class="panel login">
      <div class="mascot" role="img" aria-label="Mr Wimble, the cartoon turtle mascot with cap and stopwatch"></div>
      <h2>Connexion</h2>
      <span class="field-label" style="left:176px;top:78px">Username:</span>
      <div class="text-field" style="left:246px;top:73px;width:151px"></div>
      <span class="field-label" style="left:178px;top:110px">Password:</span>
      <div class="text-field" style="left:246px;top:105px;width:151px"></div>
      <span class="btn" style="left:246px;top:137px">Play</span>
    </section>

    <section class="panel overview">
      <h2>Game Overview</h2>
      <ul class="tabs">
        <li class="active">Your Pen</li><li>Your Allotment</li><li>Professions</li><li>Universe</li>
      </ul>
      <div class="preview-shot" role="img" aria-label="Game screenshot of a village path with players and bunnies"></div>
      <p>Breed, educate and train your bunnies in your pen. Watch as they play and grow up together under your very eyes!</p>
    </section>

    <section class="panel races">
      <h2>Take part in races with other players</h2>
      <div class="live-video">
        <svg width="42" height="50" viewBox="0 0 42 50"><path d="M0 0 L42 25 L0 50Z" fill="#ffffff"/></svg>
      </div>
    </section>

    <footer class="site-footer">Rules - General Terms and Conditions - Contact - Quintamble.com 3.0</footer>
  </main>
</div>
</body>
</html>
```